Industrial Company-Pop-Up Banner Design for Demolition and Infrastructure Company

Hi-
We need to create 2 pop-up banners for our company. They will both have the same logo, but different photos. We would like to have the colors white, red, and black and feature a modern design. I have attached some inspiration photos.

Target Market(s)

Trade Show/Job Fair Audience

Industry/Entity Type

construction, industrial

Font styles to use
Sans Serif

Colors
EB3D1F
EC4F4E
F09395
F8D3D4
FCEDEE

Requirements
Must have
• 2 versions, each with different photos but same design. Logo, Red, Black, and White Color Scheme, Modern Design
Nice to have
• Modern Design similar to the inspiration photos

```html
<!DOCTYPE html>
<html lang="en">
<head>
<meta charset="utf-8">
<title>Calloway Companies – Pop-Up Banner</title>
<link rel="stylesheet" href="https://fonts.googleapis.com/css2?family=Oswald:wght@500;600&family=Kaushan+Script&family=Montserrat:wght@600&display=swap">
<style>
  :root {
    --page-bg: #eef5fa;
    --banner-black: #1a1a1b;
    --brand-red: #de1f26;
    --white: #ffffff;
    --sky-top: #e9ecef;
    --sky-bottom: #9ea3a8;
    --site-green: #7f9a5a;
    --site-earth: #b59a72;
  }
  html, body {
    margin: 0;
    width: 1200px;
    height: 1200px;
    overflow: hidden;
    background: var(--page-bg);
  }
  .banner {
    position: absolute;
    left: 302px;
    top: 70px;
    width: 595px;
    height: 1061px;
    display: block;
  }
  .brand-name {
    font-family: "Oswald", "Arial Narrow", sans-serif;
    font-weight: 600;
    fill: var(--white);
    letter-spacing: 1px;
  }
  .tagline-lead {
    font-family: "Oswald", "Arial Narrow", sans-serif;
    font-weight: 500;
    fill: var(--white);
  }
  .tagline-script {
    font-family: "Kaushan Script", cursive;
    fill: var(--brand-red);
  }
  .since-text {
    font-family: "Montserrat", Arial, sans-serif;
    font-weight: 600;
    fill: var(--white);
    letter-spacing: 1.5px;
  }
</style>
</head>
<body>
<svg class="banner" viewBox="0 0 744 1326" xmlns="http://www.w3.org/2000/svg">
  <defs>
    <linearGradient id="plant-photo-tone" x1="0" y1="0" x2="0" y2="1">
      <stop offset="0" stop-color="var(--sky-top)"/>
      <stop offset="0.6" stop-color="var(--sky-bottom)"/>
      <stop offset="1" stop-color="#6f8a8f"/>
    </linearGradient>
    <linearGradient id="site-photo-tone" x1="1" y1="0" x2="0" y2="1">
      <stop offset="0" stop-color="var(--site-green)"/>
      <stop offset="0.45" stop-color="#c9a93a"/>
      <stop offset="1" stop-color="var(--site-earth)"/>
    </linearGradient>
  </defs>

  <rect class="banner-ground" width="744" height="1326" fill="var(--banner-black)"/>

  <g role="img" aria-label="Photo: power plant demolition with striped smokestacks and dust cloud">
    <polygon points="580,0 744,0 744,313 372,683 137,448" fill="url(#plant-photo-tone)"/>
  </g>

  <polygon class="accent-left" points="0,668 135,533 287,683 0,970" fill="var(--brand-red)"/>
  <polygon class="accent-right" points="744,393 744,703 607,838 452,683" fill="var(--brand-red)"/>

  <g role="img" aria-label="Photo: yellow excavator digging a trench on a tree-lined job site">
    <polygon points="372,688 607,923 204,1326 0,1326 0,1058" fill="url(#site-photo-tone)"/>
  </g>

  <g class="brand-lockup">
    <rect x="70" y="116" width="22" height="22" fill="var(--brand-red)"/>
    <text class="brand-name" x="104" y="138" font-size="30">CALLOWAY</text>
    <text class="brand-name" x="104" y="174" font-size="30">COMPANIES</text>
  </g>

  <g class="tagline">
    <text class="tagline-lead" x="410" y="1170" font-size="34" textLength="277" lengthAdjust="spacingAndGlyphs">SHAPING AMERICA’S</text>
    <text class="tagline-script" x="377" y="1246" font-size="92" textLength="345" lengthAdjust="spacingAndGlyphs">skyline</text>
    <rect class="since-bar" x="510" y="1258" width="234" height="33" fill="var(--brand-red)"/>
    <text class="since-text" x="527" y="1283" font-size="22">since 1959</text>
  </g>
</svg>
</body>
</html>
```